Upscale business cards needed for Board of Directors

We need professional business cards created for members of our family business Board of Directors. We would like these relatively simple and straightforward, but also with a unique element to set them apart. Probably stick with neutral and simple colors - white, grey etc. We need space for the traditional elements, including name, title, address, email/phone number. And we will be creating several from this template so it needs to be template that is easy to switch information in and out of.
Business
See description

```html
<!DOCTYPE html>
<html lang="en">
<head>
<meta charset="utf-8">
<title>Harborline Holdings – Business Card</title>
<link rel="stylesheet" href="https://fonts.googleapis.com/css2?family=Arimo:wght@400;700&display=swap">
<style>
  :root {
    --backdrop: #4a403b;
    --card: #111213;
    --card-edge: #1c1d1f;
    --ink: #f2f2f2;
    --gold: #b89a6a;
    --gloss: #2c2d30;
    --rule: #e6e6e6;
  }
  * { margin: 0; padding: 0; box-sizing: border-box; }
  html, body {
    width: 1200px; height: 864px; overflow: hidden;
    background: var(--backdrop);
    font-family: "Arimo", Arial, sans-serif;
  }
  .sheet {
    position: relative; width: 1200px; height: 864px;
  }
  .card {
    position: absolute; left: 267px; width: 665px; height: 380px;
    background: var(--card);
    border: 1px solid var(--card-edge);
    box-shadow: 0 12px 30px rgba(0,0,0,.45);
  }
  .card--back { top: 34px; }
  .card--front { top: 450px; }

  .wordmark {
    font-family: "Arimo", Arial, sans-serif;
    font-weight: 700;
    text-transform: uppercase;
    line-height: 1;
    text-align: center;
  }
  .wordmark__top { display: block; font-size: 44px; letter-spacing: 1px; }
  .wordmark__bottom { display: block; font-size: 24px; letter-spacing: 9px; margin-top: 6px; }

  .card--back .wordmark {
    position: absolute; left: 0; right: 0; top: 150px;
    color: var(--gloss);
  }

  .card--front .wordmark {
    position: absolute; right: 44px; top: 62px;
    color: var(--ink);
  }
  .card--front .wordmark__top { font-size: 38px; }
  .card--front .wordmark__bottom { font-size: 20px; letter-spacing: 8px; }

  .person { position: absolute; left: 40px; top: 148px; }
  .person__name { color: var(--gold); font-size: 21px; }
  .person__title { color: var(--ink); font-size: 16px; margin-top: 4px; }

  .divider {
    position: absolute; left: 40px; right: 44px; top: 200px;
    height: 1px; background: var(--rule);
  }

  .contact { position: absolute; left: 40px; top: 214px; list-style: none; }
  .contact__item {
    display: flex; align-items: center; gap: 10px;
    color: var(--ink); font-size: 14px; height: 23px;
  }
  .contact__icon { width: 13px; height: 13px; fill: var(--gold); flex: none; }

  .address {
    position: absolute; right: 44px; top: 298px;
    color: var(--ink); font-size: 15px; line-height: 1.5; text-align: right;
    font-style: normal;
  }
</style>
</head>
<body>
<main class="sheet">
  <section class="card card--back" aria-label="Card back">
    <div class="wordmark">
      <span class="wordmark__top">Harborline</span>
      <span class="wordmark__bottom">Holdings</span>
    </div>
  </section>

  <section class="card card--front" aria-label="Card front">
    <div class="wordmark">
      <span class="wordmark__top">Harborline</span>
      <span class="wordmark__bottom">Holdings</span>
    </div>

    <div class="person">
      <p class="person__name">Evan Marsh</p>
      <p class="person__title">President</p>
    </div>

    <div class="divider"></div>

    <ul class="contact">
      <li class="contact__item">
        <svg class="contact__icon" viewBox="0 0 16 16" aria-hidden="true">
          <path d="M3 1h3l1.5 4-2 1.3a9 9 0 0 0 4.2 4.2L11 8.5l4 1.5v3a2 2 0 0 1-2 2C6.9 15 1 9.1 1 3a2 2 0 0 1 2-2z"/>
        </svg>
        555 0142 7788
      </li>
      <li class="contact__item">
        <svg class="contact__icon" viewBox="0 0 16 16" aria-hidden="true">
          <path d="M1 3h14v1.2L8 9 1 4.2z"/><path d="M1 5.8 8 10.6l7-4.8V13H1z"/>
        </svg>
        evan@harborline.com
      </li>
      <li class="contact__item">
        <svg class="contact__icon" viewBox="0 0 16 16" aria-hidden="true">
          <circle cx="8" cy="8" r="7"/>
          <path d="M1.5 8h13M8 1.2c-2.5 3.8-2.5 9.8 0 13.6M8 1.2c2.5 3.8 2.5 9.8 0 13.6" stroke="#111213" stroke-width="1.1" fill="none"/>
        </svg>
        www.harborline.com
      </li>
    </ul>

    <address class="address">
      1720 Larkspur Avenue<br>
      Glen Hollow, NY 11020
    </address>
  </section>
</main>
</body>
</html>
```